Unusual Options Activity Graphic Card Design for Finance App

We are developing a financial data platform called Vantix Pulse, and we need a visually striking, mobile-optimized graphic card design to display unusual options activity. The card will be featured in our mobile app and marketing materials, inspired by platforms like Quorafin and Marlow Tide.
🔹 Design Goals:
Modern, clean, and professional aesthetic
Use vibrant electric blue, green, or dark theme gradients
Must feel tech-savvy and finance-oriented
Layout should be optimized for vertical mobile format (portrait)
🔹 Information to Include in the Card:
Ticker Symbol (e.g., QRV) with colored badge
Date & Time of trade
Trade Type (e.g., Sweep Call / Put)
Execution Type (At Ask or At Bid)
Strike Price
Expiration Date
Premium (e.g., $342.75K)
Size@Price (e.g., 6995@$0.49)
Volume
Open Interest
Branding at bottom: “Vantix Pulse” in modern font
🔹 Inspiration:
Quorafin’s profit/loss cards
Clean fintech dashboards (Sparvane, Marlow Tide, Kestrowe Console)
Please provide the final deliverable in high-resolution PNG and layered PSD or Figma file for future edits.
Stock Market Traders
Finance

```html
<!DOCTYPE html>
<html lang="en">
<head>
<meta charset="utf-8">
<title>Unusual Options Activity – Graphic Card Design</title>
<link href="https://fonts.googleapis.com/css2?family=Inter:wght@400;500;600;700;800&family=Plus+Jakarta+Sans:wght@700;800&display=swap" rel="stylesheet">
<style>
  :root{
    --bg:#03061a;
    --white:#ffffff;
    --green:#4fc45a;
    --green-bright:#5fd36a;
    --red:#e0403f;
    --label:#9aa6bf;
    --card-a:#213c73;
    --card-b:#13244d;
    --card-c:#0d1a3b;
    --glow-green:rgba(60,170,80,.35);
    --phone:#0b0b0f;
    --phone-line:#1d1e24;
    --web-bar:#1c1c20;
    --web-body:#121214;
    --field:#2a2a2e;
    --safari:#2b2b2e;
  }
  *{box-sizing:border-box;margin:0;padding:0}
  html,body{width:1200px;height:975px;overflow:hidden;background:var(--bg)}
  body{position:relative;font-family:"Inter",sans-serif;color:var(--white)}

  .board-title{position:absolute;left:40px;top:32px;width:320px;text-align:center;
    font-family:"Plus Jakarta Sans",sans-serif;font-weight:800;font-size:20px;line-height:24.5px;letter-spacing:-.3px}

  .annotation{position:absolute;font-family:"Plus Jakarta Sans",sans-serif;font-weight:800;font-size:13.5px;white-space:nowrap;line-height:1}
  .annotation--right-aligned{text-align:right}
  .connectors{position:absolute;left:0;top:0;width:1200px;height:975px;pointer-events:none}

  .section-label{position:absolute;font-family:"Plus Jakarta Sans",sans-serif;font-weight:800;font-size:17px;transform:translateX(-50%)}

  /* ---------- flow card ---------- */
  .flow-card{position:absolute;width:129px;height:171px;border-radius:5px;overflow:hidden;
    background:linear-gradient(165deg,var(--card-a) 0%,var(--card-b) 55%,#1a3570 100%)}
  .flow-card--glow{background:
      radial-gradient(ellipse at 70% 30%,var(--glow-green),transparent 60%),
      radial-gradient(ellipse at 20% 90%,rgba(40,120,70,.35),transparent 60%),
      linear-gradient(165deg,#16305a 0%,#0f213f 55%,#102a4d 100%)}
  .flow-card--deep{background:
      radial-gradient(ellipse at 50% 110%,rgba(60,170,80,.35),transparent 55%),
      linear-gradient(170deg,#1c3466 0%,#112350 60%,#0f2450 100%)}
  .flow-card__stamp{position:absolute;left:12px;top:12.5px;height:13.5px;display:flex;align-items:stretch;
    border:1px solid #c9ced8;border-radius:2px;font-size:7.5px;line-height:11.5px}
  .flow-card__ticker{background:var(--green);color:#0c1a0d;font-weight:700;padding:0 5px;border-radius:1px}
  .flow-card__ticker--red{background:var(--red);color:#2a0707}
  .flow-card__time{padding:0 6px;color:#f1f3f8;font-weight:500}
  .flow-card__title{position:absolute;left:11px;top:33px;font-size:17px;font-weight:700;letter-spacing:.2px;line-height:20px;white-space:nowrap}
  .is-call{color:var(--green-bright)}
  .is-put{color:var(--red)}
  .flow-card__exec{position:absolute;left:11.5px;top:54px;font-size:8.3px;font-weight:500;letter-spacing:.1px}
  .flow-card__stats{position:absolute;left:11.5px;top:70px;display:grid;grid-template-columns:53px 60px;row-gap:5.2px}
  .stat__label{display:block;font-size:5.3px;color:var(--label);letter-spacing:.2px;line-height:7px}
  .stat__value{display:block;font-size:8.3px;font-weight:700;line-height:10px;white-space:nowrap}
  .flow-card__brand{position:absolute;right:8px;bottom:11px;display:flex;align-items:center;gap:2px;
    font-size:4.6px;font-weight:700;letter-spacing:.2px;color:var(--white)}
  .flow-card__brand-dot{width:5px;height:5px;border-radius:50%;background:var(--green)}

  /* ---------- phone app ---------- */
  .phone{position:absolute;left:101px;top:585px;width:164px;height:356px;border-radius:11px;background:var(--phone);overflow:hidden}
  .status-bar{position:absolute;left:0;top:0;width:100%;height:22px;font-size:6.8px;font-weight:600}
  .status-bar__time{position:absolute;left:20px;top:9px}
  .status-bar__icons{position:absolute;right:16px;top:9px;display:flex;gap:3px;align-items:center}
  .phone__heading{position:absolute;top:25px;width:100%;text-align:center;font-size:7.5px;font-weight:500}
  .phone__tabs{position:absolute;top:41px;left:6px;display:flex;gap:12px;font-size:5.3px;white-space:nowrap}
  .phone__tabs .is-active{color:var(--green)}
  .phone__rule{position:absolute;left:0;top:54px;width:100%;height:1px;background:var(--phone-line)}
  .phone__nav{position:absolute;left:0;bottom:0;width:100%;height:35px;background:var(--phone);display:flex;justify-content:space-around;align-items:flex-start;padding-top:8px}
  .phone__nav-item{display:flex;flex-direction:column;align-items:center;font-size:5px;color:#b8bcc6;gap:1px}
  .phone__nav-item.is-active{color:var(--green)}
  .home-bar{position:absolute;bottom:4px;left:50%;width:59px;height:2px;border-radius:2px;background:#e6e6e6;transform:translateX(-50%)}

  /* ---------- web app ---------- */
  .web{position:absolute;left:290px;top:583px;width:166px;height:358px;border-radius:9px;background:var(--web-body);overflow:hidden}
  .web .status-bar{background:#fff;color:#111;height:24px}
  .web .status-bar__time{left:19px;top:8px}
  .web .status-bar__icons{top:8px;right:15px}
  .web__header{position:absolute;top:24px;left:0;width:100%;height:35px;background:var(--web-bar);font-size:6px}
  .web__logo-dot{position:absolute;left:4px;top:11px;width:11px;height:11px;border-radius:50%;border:1.5px solid var(--green)}
  .web__header-title{position:absolute;left:23px;top:14px;font-weight:500}
  .toggle{position:absolute;width:22px;height:10px;border-radius:6px;background:#fff}
  .toggle::after{content:"";position:absolute;left:1.5px;top:1.5px;width:7px;height:7px;border-radius:50%;background:#111}
  .web__avatar{position:absolute;left:120px;top:12px;width:11px;height:11px;border-radius:50%;background:#8a93a8}
  .web__body-title{position:absolute;left:4px;top:64px;font-size:7.6px;font-weight:500}
  .switch{position:absolute;width:11px;height:6px;border-radius:4px;background:#fff}
  .switch::after{content:"";position:absolute;left:1px;top:1px;width:4px;height:4px;border-radius:50%;background:#111}
  .web__auto{position:absolute;left:22px;top:84px;font-size:5.4px}
  .web__search{position:absolute;left:4px;top:103px;width:155px;height:15px;border-radius:2px;background:var(--field);font-size:5.4px;color:#b4b6bc;padding:4.5px 6px}
  .web__tools{position:absolute;left:12px;top:125px;display:flex;gap:8px;font-size:5.2px;align-items:center}
  .web__tools span{display:flex;align-items:center;gap:3px}
  .web__safari{position:absolute;left:0;bottom:0;width:100%;height:48px;background:var(--safari)}
  .web__url{position:absolute;left:14px;top:4px;width:138px;height:15px;border-radius:5px;background:#3a3a3e;font-size:5.8px;text-align:center;line-height:15px;color:#e8e8ea}
  .web__safari-icons{position:absolute;left:8px;top:24px;width:150px;display:flex;justify-content:space-between}

  /* ---------- closing ---------- */
  .thanks{position:absolute;left:825px;top:840px;width:400px;text-align:center}
  .thanks__title{font-family:"Inter",sans-serif;font-weight:800;font-size:45px;letter-spacing:-2px;line-height:50px}
  .thanks__note{margin-top:5px;font-size:15.5px;line-height:19px;font-weight:400}
</style>
</head>
<body>

<h1 class="board-title">Unusual Options Activity :<br>Graphic Card Design for<br>Finance App</h1>

<!-- anatomy annotations -->
<span class="annotation" style="left:87px;top:243px">Ticker Symbol</span>
<span class="annotation" style="left:104px;top:264px">Trade Type</span>
<span class="annotation" style="left:77px;top:283px">Execution Type</span>
<span class="annotation" style="left:387px;top:235px">Date &amp; Time of trade</span>
<span class="annotation" style="left:408px;top:264px">C/P</span>
<span class="annotation" style="left:408px;top:373px">Branding</span>

<svg class="connectors" viewBox="0 0 1200 975" aria-hidden="true">
  <defs>
    <marker id="tip" viewBox="0 0 6 6" refX="5" refY="3" markerWidth="5" markerHeight="5" orient="auto">
      <path d="M0 0 L6 3 L0 6 Z" fill="#fff"/>
    </marker>
  </defs>
  <g fill="none" stroke="#fff" stroke-width="0.9">
    <path d="M186 250 Q205 230 231 245" marker-end="url(#tip)"/>
    <path d="M183 272 Q200 263 230 268" marker-end="url(#tip)"/>
    <path d="M183 289 Q200 280 230 284" marker-end="url(#tip)"/>
    <path d="M383 242 Q366 228 352 246" marker-end="url(#tip)"/>
    <path d="M403 272 Q380 258 346 272" marker-end="url(#tip)"/>
    <path d="M397 384 Q378 365 352 382" marker-end="url(#tip)"/>
  </g>
  <g fill="#fff">
    <circle cx="186" cy="250" r="1.6"/><circle cx="183" cy="272" r="1.6"/><circle cx="183" cy="289" r="1.6"/>
    <circle cx="383" cy="242" r="1.6"/><circle cx="403" cy="272" r="1.6"/><circle cx="397" cy="384" r="1.6"/>
  </g>
</svg>

<!-- anatomy card -->
<article class="flow-card flow-card--deep" style="left:224px;top:228px">
  <div class="flow-card__stamp"><span class="flow-card__ticker">GXD</span><span class="flow-card__time">04/05/25 | 10:32:12</span></div>
  <h2 class="flow-card__title">TRADE <span class="is-call">CALL</span></h2>
  <p class="flow-card__exec is-call">AT ASk</p>
  <dl class="flow-card__stats">
    <div><dt class="stat__label">STRIKE</dt><dd class="stat__value">$91</dd></div>
    <div><dt class="stat__label">EXPIRATION</dt><dd class="stat__value">19 Apr 25</dd></div>
    <div><dt class="stat__label">PREMIUM</dt><dd class="stat__value">$342.75K</dd></div>
    <div><dt class="stat__label">SIZE@PRICE</dt><dd class="stat__value">6995@$0.49</dd></div>
    <div><dt class="stat__label">VOLUME</dt><dd class="stat__value">34.7K</dd></div>
    <div><dt class="stat__label">OPEN INTEREST</dt><dd class="stat__value">2424</dd></div>
  </dl>
  <div class="flow-card__brand"><span class="flow-card__brand-dot"></span>VANTIX PULSE</div>
</article>

<!-- variant grid: row one -->
<article class="flow-card" style="left:585px;top:228px">
  <div class="flow-card__stamp"><span class="flow-card__ticker">GXD</span><span class="flow-card__time">04/05/25 | 10:32:12</span></div>
  <h2 class="flow-card__title">SWEEP <span class="is-put">PUT</span></h2>
  <p class="flow-card__exec is-call">AT ASK</p>
  <dl class="flow-card__stats">
    <div><dt class="stat__label">STRIKE</dt><dd class="stat__value">$91</dd></div>
    <div><dt class="stat__label">EXPIRATION</dt><dd class="stat__value">19 Apr 25</dd></div>
    <div><dt class="stat__label">PREMIUM</dt><dd class="stat__value">$342.75K</dd></div>
    <div><dt class="stat__label">SIZE@PRICE</dt><dd class="stat__value">6995@$0.49</dd></div>
    <div><dt class="stat__label">VOLUME</dt><dd class="stat__value">34.7K</dd></div>
    <div><dt class="stat__label">OPEN INTEREST</dt><dd class="stat__value">2424</dd></div>
  </dl>
  <div class="flow-card__brand"><span class="flow-card__brand-dot"></span>VANTIX PULSE</div>
</article>

<article class="flow-card flow-card--glow" style="left:722px;top:228px">
  <div class="flow-card__stamp"><span class="flow-card__ticker">GXD</span><span class="flow-card__time">04/05/25 | 10:32:12</span></div>
  <h2 class="flow-card__title">TRADE <span class="is-call">CALL</span></h2>
  <p class="flow-card__exec is-put">AT BID</p>
  <dl class="flow-card__stats">
    <div><dt class="stat__label">STRIKE</dt><dd class="stat__value">$91</dd></div>
    <div><dt class="stat__label">EXPIRATION</dt><dd class="stat__value">19 Apr 25</dd></div>
    <div><dt class="stat__label">PREMIUM</dt><dd class="stat__value">$342.75K</dd></div>
    <div><dt class="stat__label">SIZE@PRICE</dt><dd class="stat__value">6995@$0.49</dd></div>
    <div><dt class="stat__label">VOLUME</dt><dd class="stat__value">34.7K</dd></div>
    <div><dt class="stat__label">OPEN INTEREST</dt><dd class="stat__value">2424</dd></div>
  </dl>
  <div class="flow-card__brand"><span class="flow-card__brand-dot"></span>VANTIX PULSE</div>
</article>

<article class="flow-card flow-card--deep" style="left:860px;top:228px">
  <div class="flow-card__stamp"><span class="flow-card__ticker">GXD</span><span class="flow-card__time">04/05/25 | 10:32:12</span></div>
  <h2 class="flow-card__title">TRADE <span class="is-call">CALL</span></h2>
  <p class="flow-card__exec is-call">AT ASK</p>
  <dl class="flow-card__stats">
    <div><dt class="stat__label">STRIKE</dt><dd class="stat__value">$91</dd></div>
    <div><dt class="stat__label">EXPIRATION</dt><dd class="stat__value">19 Apr 25</dd></div>
    <div><dt class="stat__label">PREMIUM</dt><dd class="stat__value">$342.75K</dd></div>
    <div><dt class="stat__label">SIZE@PRICE</dt><dd class="stat__value">6995@$0.49</dd></div>
    <div><dt class="stat__label">VOLUME</dt><dd class="stat__value">34.7K</dd></div>
    <div><dt class="stat__label">OPEN INTEREST</dt><dd class="stat__value">2424</dd></div>
  </dl>
  <div class="flow-card__brand"><span class="flow-card__brand-dot"></span>VANTIX PULSE</div>
</article>

<article class="flow-card flow-card--glow" style="left:997px;top:228px">
  <div class="flow-card__stamp"><span class="flow-card__ticker">GXD</span><span class="flow-card__time">04/05/25 | 10:32:12</span></div>
  <h2 class="flow-card__title">TRADE <span class="is-put">PUT</span></h2>
  <p class="flow-card__exec is-put">AT BID</p>
  <dl class="flow-card__stats">
    <div><dt class="stat__label">STRIKE</dt><dd class="stat__value">$91</dd></div>
    <div><dt class="stat__label">EXPIRATION</dt><dd class="stat__value">19 Apr 25</dd></div>
    <div><dt class="stat__label">PREMIUM</dt><dd class="stat__value">$342.75K</dd></div>
    <div><dt class="stat__label">SIZE@PRICE</dt><dd class="stat__value">6995@$0.49</dd></div>
    <div><dt class="stat__label">VOLUME</dt><dd class="stat__value">34.7K</dd></div>
    <div><dt class="stat__label">OPEN INTEREST</dt><dd class="stat__value">2424</dd></div>
  </dl>
  <div class="flow-card__brand"><span class="flow-card__brand-dot"></span>VANTIX PULSE</div>
</article>

<!-- variant grid: row two -->
<article class="flow-card" style="left:585px;top:460px">
  <div class="flow-card__stamp"><span class="flow-card__ticker flow-card__ticker--red">GXD</span><span class="flow-card__time">04/05/25 | 10:32:12</span></div>
  <h2 class="flow-card__title">SWEEP <span class="is-put">PUT</span></h2>
  <p class="flow-card__exec is-call">AT ASK</p>
  <dl class="flow-card__stats">
    <div><dt class="stat__label">STRIKE</dt><dd class="stat__value">$91</dd></div>
    <div><dt class="stat__label">EXPIRATION</dt><dd class="stat__value">19 Apr 25</dd></div>
    <div><dt class="stat__label">PREMIUM</dt><dd class="stat__value">$342.75K</dd></div>
    <div><dt class="stat__label">SIZE@PRICE</dt><dd class="stat__value">6995@$0.49</dd></div>
    <div><dt class="stat__label">VOLUME</dt><dd class="stat__value">34.7K</dd></div>
    <div><dt class="stat__label">OPEN INTEREST</dt><dd class="stat__value">2424</dd></div>
  </dl>
  <div class="flow-card__brand"><span class="flow-card__brand-dot"></span>VANTIX PULSE</div>
</article>

<article class="flow-card flow-card--glow" style="left:719px;top:460px">
  <div class="flow-card__stamp"><span class="flow-card__ticker flow-card__ticker--red">GXD</span><span class="flow-card__time">04/05/25 | 10:32:12</span></div>
  <h2 class="flow-card__title">SWEEP <span class="is-call">CALL</span></h2>
  <p class="flow-card__exec is-put">AT BID</p>
  <dl class="flow-card__stats">
    <div><dt class="stat__label">STRIKE</dt><dd class="stat__value">$91</dd></div>
    <div><dt class="stat__label">EXPIRATION</dt><dd class="stat__value">19 Apr 25</dd></div>
    <div><dt class="stat__label">PREMIUM</dt><dd class="stat__value">$342.75K</dd></div>
    <div><dt class="stat__label">SIZE@PRICE</dt><dd class="stat__value">6995@$0.49</dd></div>
    <div><dt class="stat__label">VOLUME</dt><dd class="stat__value">34.7K</dd></div>
    <div><dt class="stat__label">OPEN INTEREST</dt><dd class="stat__value">2424</dd></div>
  </dl>
  <div class="flow-card__brand"><span class="flow-card__brand-dot"></span>VANTIX PULSE</div>
</article>

<article class="flow-card flow-card--deep" style="left:853px;top:460px">
  <div class="flow-card__stamp"><span class="flow-card__ticker flow-card__ticker--red">GXD</span><span class="flow-card__time">04/05/25 | 10:32:12</span></div>
  <h2 class="flow-card__title">TRADE <span class="is-call">CALL</span></h2>
  <p class="flow-card__exec is-put">AT ASK</p>
  <dl class="flow-card__stats">
    <div><dt class="stat__label">STRIKE</dt><dd class="stat__value">$91</dd></div>
    <div><dt class="stat__label">EXPIRATION</dt><dd class="stat__value">19 Apr 25</dd></div>
    <div><dt class="stat__label">PREMIUM</dt><dd class="stat__value">$342.75K</dd></div>
    <div><dt class="stat__label">SIZE@PRICE</dt><dd class="stat__value">6995@$0.49</dd></div>
    <div><dt class="stat__label">VOLUME</dt><dd class="stat__value">34.7K</dd></div>
    <div><dt class="stat__label">OPEN INTEREST</dt><dd class="stat__value">2424</dd></div>
  </dl>
  <div class="flow-card__brand"><span class="flow-card__brand-dot"></span>VANTIX PULSE</div>
</article>

<article class="flow-card flow-card--deep" style="left:987px;top:460px">
  <div class="flow-card__stamp"><span class="flow-card__ticker flow-card__ticker--red">GXD</span><span class="flow-card__time">04/05/25 | 10:32:12</span></div>
  <h2 class="flow-card__title">TRADE <span class="is-put">PUT</span></h2>
  <p class="flow-card__exec is-put">AT ASK</p>
  <dl class="flow-card__stats">
    <div><dt class="stat__label">STRIKE</dt><dd class="stat__value">$91</dd></div>
    <div><dt class="stat__label">EXPIRATION</dt><dd class="stat__value">19 Apr 25</dd></div>
    <div><dt class="stat__label">PREMIUM</dt><dd class="stat__value">$342.75K</dd></div>
    <div><dt class="stat__label">SIZE@PRICE</dt><dd class="stat__value">6995@$0.49</dd></div>
    <div><dt class="stat__label">VOLUME</dt><dd class="stat__value">34.7K</dd></div>
    <div><dt class="stat__label">OPEN INTEREST</dt><dd class="stat__value">2424</dd></div>
  </dl>
  <div class="flow-card__brand"><span class="flow-card__brand-dot"></span>VANTIX PULSE</div>
</article>

<!-- platform previews -->
<h2 class="section-label" style="left:175px;top:546px">APP</h2>
<h2 class="section-label" style="left:370px;top:542px">Web APP</h2>

<section class="phone" aria-label="Mobile app screen">
  <div class="status-bar">
    <span class="status-bar__time">7:09 ●</span>
    <span class="status-bar__icons">
      <svg width="9" height="6" viewBox="0 0 9 6"><g fill="#fff"><rect x="0" y="4" width="1.5" height="2"/><rect x="2.5" y="3" width="1.5" height="3"/><rect x="5" y="1.5" width="1.5" height="4.5"/><rect x="7.5" y="0" width="1.5" height="6"/></g></svg>
      <svg width="8" height="6" viewBox="0 0 8 6"><path d="M0 2 Q4 -1 8 2 L4 6 Z" fill="#fff"/></svg>
      <svg width="12" height="6" viewBox="0 0 12 6"><rect x=".5" y=".5" width="10" height="5" rx="1.5" fill="#fff"/><rect x="11" y="2" width="1" height="2" fill="#fff"/></svg>
    </span>
  </div>
  <p class="phone__heading">Markets</p>
  <nav class="phone__tabs"><span class="is-active">Option Flow</span><span>Darkpool</span><span>Treemap</span><span>Gamma</span><span>Snaps</span></nav>
  <div class="phone__rule"></div>
</section>

<article class="flow-card" style="left:119px;top:649px">
  <div class="flow-card__stamp"><span class="flow-card__ticker">GXD</span><span class="flow-card__time">04/05/25 | 10:32:12</span></div>
  <h2 class="flow-card__title">TRADE <span class="is-call">CALL</span></h2>
  <p class="flow-card__exec is-call">AT ASK</p>
  <dl class="flow-card__stats">
    <div><dt class="stat__label">STRIKE</dt><dd class="stat__value">$91</dd></div>
    <div><dt class="stat__label">EXPIRATION</dt><dd class="stat__value">19 Apr 25</dd></div>
    <div><dt class="stat__label">PREMIUM</dt><dd class="stat__value">$342.75K</dd></div>
    <div><dt class="stat__label">SIZE@PRICE</dt><dd class="stat__value">6995@$0.49</dd></div>
    <div><dt class="stat__label">VOLUME</dt><dd class="stat__value">34.7K</dd></div>
    <div><dt class="stat__label">OPEN INTEREST</dt><dd class="stat__value">2424</dd></div>
  </dl>
  <div class="flow-card__brand"><span class="flow-card__brand-dot"></span>VANTIX PULSE</div>
</article>

<article class="flow-card" style="left:119px;top:829px;height:78px;border-radius:5px 5px 0 0">
  <div class="flow-card__stamp"><span class="flow-card__ticker">GXD</span><span class="flow-card__time">04/05/25 | 10:32:12</span></div>
  <h2 class="flow-card__title">TRADE <span class="is-call">CALL</span></h2>
  <p class="flow-card__exec is-call">AT ASK</p>
  <dl class="flow-card__stats">
    <div><dt class="stat__label">STRIKE</dt></div>
    <div><dt class="stat__label">EXPIRATION</dt></div>
  </dl>
</article>

<nav class="phone__nav" style="position:absolute;left:101px;top:906px;width:164px;height:35px;bottom:auto;border-radius:0 0 11px 11px">
  <span class="phone__nav-item"><svg width="7" height="7" viewBox="0 0 7 7"><g fill="#b8bcc6"><rect width="3" height="3"/><rect x="4" width="3" height="3"/><rect y="4" width="3" height="3"/><rect x="4" y="4" width="3" height="3"/></g></svg></span>
  <span class="phone__nav-item"><svg width="6" height="7" viewBox="0 0 6 7"><rect width="6" height="7" rx="1" fill="#b8bcc6"/><g stroke="#0b0b0f" stroke-width=".7"><line x1="1" y1="2.5" x2="5" y2="2.5"/><line x1="1" y1="4.5" x2="5" y2="4.5"/></g></svg></span>
  <span class="phone__nav-item is-active"><svg width="8" height="5" viewBox="0 0 8 5"><path d="M0 4.5 L3 2 L5 3.5 L8 .5" fill="none" stroke="#4fc45a" stroke-width="1"/></svg>Markets</span>
  <span class="phone__nav-item"><svg width="7" height="7" viewBox="0 0 7 7"><g fill="#b8bcc6"><rect x="0" y="3" width="1.8" height="4"/><rect x="2.6" y="0" width="1.8" height="7"/><rect x="5.2" y="2" width="1.8" height="5"/></g></svg></span>
  <span class="phone__nav-item"><svg width="7" height="7" viewBox="0 0 7 7"><circle cx="3.5" cy="2" r="1.8" fill="#b8bcc6"/><path d="M0 7 Q3.5 2.5 7 7 Z" fill="#b8bcc6"/></svg></span>
  <span class="home-bar"></span>
</nav>

<section class="web" aria-label="Web app screen">
  <div class="status-bar">
    <span class="status-bar__time">7:09 ●</span>
    <span class="status-bar__icons">
      <svg width="9" height="6" viewBox="0 0 9 6"><g fill="#111"><rect x="0" y="4" width="1.5" height="2"/><rect x="2.5" y="3" width="1.5" height="3"/><rect x="5" y="1.5" width="1.5" height="4.5"/><rect x="7.5" y="0" width="1.5" height="6"/></g></svg>
      <svg width="8" height="6" viewBox="0 0 8 6"><path d="M0 2 Q4 -1 8 2 L4 6 Z" fill="#111"/></svg>
      <svg width="12" height="6" viewBox="0 0 12 6"><rect x=".5" y=".5" width="10" height="5" rx="1.5" fill="#111"/><rect x="11" y="2" width="1" height="2" fill="#111"/></svg>
    </span>
  </div>
  <header class="web__header">
    <span class="web__logo-dot"></span>
    <span class="web__header-title">Option Flow</span>
    <span class="toggle" style="left:91px;top:12.5px"></span>
    <span class="web__avatar"></span>
    <svg style="position:absolute;left:137px;top:16px" width="5" height="3" viewBox="0 0 5 3"><path d="M0 0 L2.5 3 L5 0" fill="none" stroke="#ddd" stroke-width=".8"/></svg>
    <svg style="position:absolute;left:152px;top:15px" width="6" height="5" viewBox="0 0 6 5"><g stroke="#ddd" stroke-width=".8"><line x1="0" y1=".5" x2="6" y2=".5"/><line x1="0" y1="2.5" x2="6" y2="2.5"/><line x1="0" y1="4.5" x2="6" y2="4.5"/></g></svg>
  </header>
  <p class="web__body-title">Option Flow Data</p>
  <span class="switch" style="left:5px;top:85px"></span>
  <span class="web__auto">Auto Refresh</span>
  <div class="web__search">Search Ticker...</div>
  <div class="web__tools">
    <span><svg width="8" height="5" viewBox="0 0 8 5"><g stroke="#fff" stroke-width=".8"><line x1="0" y1=".5" x2="8" y2=".5"/><line x1="1.5" y1="2.5" x2="6.5" y2="2.5"/><line x1="3" y1="4.5" x2="5" y2="4.5"/></g></svg>Filter</span>
    <span><svg width="6" height="7" viewBox="0 0 6 7"><path d="M1 3 V6.5 H5 V3 M3 5 V.5 M1.8 1.7 L3 .5 L4.2 1.7" fill="none" stroke="#fff" stroke-width=".7"/></svg>Export</span>
  </div>
  <article class="flow-card flow-card--glow" style="left:16px;top:143px;height:167px;border-radius:5px 5px 0 0">
    <div class="flow-card__stamp"><span class="flow-card__ticker">GXD</span><span class="flow-card__time">04/05/25 | 10:32:12</span></div>
    <h2 class="flow-card__title">TRADE <span class="is-call">CALL</span></h2>
    <p class="flow-card__exec is-call">AT ASk</p>
    <dl class="flow-card__stats">
      <div><dt class="stat__label">STRIKE</dt><dd class="stat__value">$91</dd></div>
      <div><dt class="stat__label">EXPIRATION</dt><dd class="stat__value">19 Apr 25</dd></div>
      <div><dt class="stat__label">PREMIUM</dt><dd class="stat__value">$342.75K</dd></div>
      <div><dt class="stat__label">SIZE@PRICE</dt><dd class="stat__value">6995@$0.49</dd></div>
      <div><dt class="stat__label">VOLUME</dt><dd class="stat__value">34.7K</dd></div>
      <div><dt class="stat__label">OPEN INTEREST</dt><dd class="stat__value">2424</dd></div>
    </dl>
    <div class="flow-card__brand" style="bottom:7px"><span class="flow-card__brand-dot"></span>VANTIX PULSE</div>
  </article>
  <div class="web__safari">
    <div class="web__url">🔒 app.vantixpulse.com</div>
    <div class="web__safari-icons">
      <svg width="6" height="8" viewBox="0 0 6 8"><path d="M5 0.5 L1 4 L5 7.5" fill="none" stroke="#3a8dff" stroke-width="1"/></svg>
      <svg width="6" height="8" viewBox="0 0 6 8"><path d="M1 0.5 L5 4 L1 7.5" fill="none" stroke="#666" stroke-width="1"/></svg>
      <svg width="7" height="9" viewBox="0 0 7 9"><path d="M1 4 V8.5 H6 V4 M3.5 6 V.5 M2 2 L3.5 .5 L5 2" fill="none" stroke="#3a8dff" stroke-width=".8"/></svg>
      <svg width="9" height="7" viewBox="0 0 9 7"><path d="M.5 1 Q2.5 0 4.5 1.2 Q6.5 0 8.5 1 V6.5 Q6.5 5.5 4.5 6.5 Q2.5 5.5 .5 6.5 Z M4.5 1.2 V6.5" fill="none" stroke="#3a8dff" stroke-width=".8"/></svg>
      <svg width="8" height="8" viewBox="0 0 8 8"><rect x=".5" y="2.5" width="5" height="5" rx="1" fill="none" stroke="#3a8dff" stroke-width=".8"/><path d="M2.5 .5 H7.5 V5.5" fill="none" stroke="#3a8dff" stroke-width=".8"/></svg>
    </div>
    <span class="home-bar"></span>
  </div>
</section>

<footer class="thanks">
  <p class="thanks__title">Thank you</p>
  <p class="thanks__note">Your feedback matters to us. Let us<br>know what you think!</p>
</footer>

</body>
</html>
```